Now Leasing Banner

Looking for a banner that says the following information approx 4' x 30'

Now Leasing Maplebrook Terrace 925-318-6042

Target Market(s)

Drive by traffic

Industry/Entity Type

Residential property management

Requirements
Must have
• Clear and readable from a distance

```html
<!DOCTYPE html>
<html lang="en">
<head>
<meta charset="utf-8">
<title>Now Leasing Banner – Maplebrook Terrace</title>
<link rel="stylesheet" href="https://fonts.googleapis.com/css2?family=Great+Vibes&family=Oswald:wght@600;700&display=swap">
<style>
  :root {
    --page-bg: #ffffff;
    --banner-green: #34564a;
    --banner-edge: #c9cfcb;
    --sepia-light: #e6ddcc;
    --sepia-mid: #b59a72;
    --sepia-dark: #7a5a2e;
    --cream: #ecebdc;
    --white: #ffffff;
    --phone-box-top: #f1f1ea;
    --phone-box-bottom: #d9dfc8;
    --phone-brown: #6a451c;
  }
  html, body {
    margin: 0;
    padding: 0;
    width: 1200px;
    height: 325px;
    overflow: hidden;
    background: var(--page-bg);
  }
  .canvas {
    position: relative;
    width: 1200px;
    height: 325px;
  }
  .banner {
    position: absolute;
    left: 41px;
    top: 87px;
    width: 1125px;
    height: 151px;
    background: var(--banner-green);
    border: 1px solid var(--banner-edge);
    box-shadow: 0 1px 2px rgba(0,0,0,0.18);
    box-sizing: border-box;
    overflow: hidden;
  }
  .property-illustration {
    position: absolute;
    left: 0;
    top: 0;
    width: 251px;
    height: 100%;
    background: linear-gradient(180deg, var(--sepia-light) 0%, var(--sepia-mid) 60%, var(--sepia-dark) 100%);
  }
  .property-name {
    position: absolute;
    left: 268px;
    top: 4px;
    width: 380px;
    margin: 0;
    font-family: "Great Vibes", cursive;
    font-weight: 400;
    color: var(--cream);
    line-height: 1;
  }
  .property-name .line-one {
    display: block;
    font-size: 74px;
  }
  .property-name .line-two {
    display: block;
    font-size: 66px;
    margin-top: -14px;
    padding-left: 110px;
  }
  .headline {
    position: absolute;
    left: 656px;
    top: 6px;
    width: 436px;
    margin: 0;
    font-family: "Oswald", sans-serif;
    font-weight: 700;
    font-size: 70px;
    line-height: 1;
    color: var(--white);
    letter-spacing: 0.5px;
    text-align: center;
    white-space: nowrap;
  }
  .phone-box {
    position: absolute;
    left: 656px;
    top: 76px;
    width: 436px;
    height: 75px;
    background: linear-gradient(180deg, var(--phone-box-top) 0%, var(--phone-box-bottom) 100%);
    display: flex;
    align-items: center;
    justify-content: center;
  }
  .phone-number {
    font-family: "Oswald", sans-serif;
    font-weight: 600;
    font-size: 66px;
    line-height: 1;
    color: var(--phone-brown);
    letter-spacing: 3px;
    white-space: nowrap;
  }
</style>
</head>
<body>
  <div class="canvas">
    <div class="banner">
      <div class="property-illustration" role="img" aria-label="Sepia engraving-style illustration of the two-storey townhome community framed by trees and a picket fence"></div>
      <h1 class="property-name">
        <span class="line-one">Maplebrook</span>
        <span class="line-two">Terrace</span>
      </h1>
      <p class="headline">NOW LEASING</p>
      <div class="phone-box">
        <span class="phone-number">925-318-6042</span>
      </div>
    </div>
  </div>
</body>
</html>
```